"Harbor Builders" is a residential building company and needs a new business card design and may re

We would like a redesign based on the existing logo, and would like to see a new font as well. We are bespoke home builders who build sustainable energy efficient homes.

Industry/Entity Type

Construction

Contact Information for Business Card

Business card size 40mm x 90mm

Colors

Designer to choose colors to be used in the design.

```html
<!DOCTYPE html>
<html lang="en">
<head>
<meta charset="utf-8">
<title>Harbor Builders – Business Card</title>
<link rel="stylesheet" href="https://fonts.googleapis.com/css2?family=Open+Sans:wght@600&family=Roboto+Condensed:wght@700&family=Roboto:wght@400;500&display=swap">
<style>
  :root {
    --backdrop: #5b4838;
    --card-light: #f3f3f3;
    --card-dark: #070809;
    --ink: #111111;
    --ink-soft: #4a4a4a;
    --accent: #a8c43a;
    --rule: #b5b5b5;
    --on-dark: #f2f2f2;
    --url-dark: #d6d6d6;
  }
  * { margin: 0; padding: 0; box-sizing: border-box; }
  html, body {
    width: 1200px; height: 960px; overflow: hidden;
    background: var(--backdrop);
  }
  .card {
    position: absolute;
    width: 600px; height: 343px;
  }
  .card-front { left: 314px; top: 113px; background: var(--card-light); }
  .card-back  { left: 311px; top: 472px; background: var(--card-dark); }

  .brand {
    position: absolute;
    display: flex; align-items: center; gap: 10px;
    font-family: "Open Sans", sans-serif;
    font-weight: 600;
    white-space: nowrap;
  }
  .brand-mark { display: block; background: var(--accent); }
  .card-front .brand { left: 36px; top: 148px; font-size: 27px; color: var(--ink); }
  .card-front .brand-mark { width: 22px; height: 22px; }
  .card-back .brand { left: 0; right: 0; justify-content: center; top: 122px; font-size: 44px; color: var(--on-dark); }
  .card-back .brand-mark { width: 34px; height: 34px; }

  .divider {
    position: absolute; left: 296px; top: 72px;
    width: 1px; height: 206px;
    background: linear-gradient(to bottom, transparent, var(--rule) 20%, var(--rule) 80%, transparent);
  }
  .contact {
    position: absolute; left: 320px; top: 76px;
    font-family: "Roboto", sans-serif;
    font-size: 14.5px; line-height: 18px;
    color: var(--ink-soft);
  }
  .contact-name {
    font-family: "Roboto Condensed", sans-serif;
    font-weight: 700; font-size: 22px; line-height: 26px;
    color: var(--ink); margin-bottom: 10px;
  }
  .contact-company { font-weight: 500; font-size: 14px; }
  .contact-address { margin-bottom: 3px; }
  .contact-ids { margin-bottom: 6px; }
  .contact-line { display: flex; align-items: center; gap: 8px; line-height: 19px; }
  .contact-line svg { width: 13px; height: 13px; flex: none; fill: var(--ink); }

  .url-back {
    position: absolute; left: 0; right: 0; top: 297px;
    text-align: center;
    font-family: "Roboto", sans-serif;
    font-size: 14px; letter-spacing: 2.6px;
    color: var(--url-dark);
  }
</style>
</head>
<body>
  <section class="card card-front">
    <div class="brand"><span class="brand-mark"></span>Harbor Builders</div>
    <div class="divider"></div>
    <div class="contact">
      <p class="contact-name">DANIEL MORETTI</p>
      <div class="contact-address">
        <p class="contact-company">Harbor Builders Pty Ltd</p>
        <p>PO Box 4120 Eastgate</p>
        <p>LPO Riverton WA 6148</p>
      </div>
      <div class="contact-ids">
        <p>Registration 40871</p>
        <p>ABN: 52 304 719 668</p>
      </div>
      <p class="contact-line">
        <svg viewBox="0 0 13 13" aria-hidden="true"><path d="M3.5 0h6a1 1 0 0 1 1 1v11a1 1 0 0 1-1 1h-6a1 1 0 0 1-1-1V1a1 1 0 0 1 1-1zm.5 1.5v8.5h5V1.5zm2.5 9.3a.8.8 0 1 0 0 1.6.8.8 0 0 0 0-1.6z"/></svg>
        0412 555 019
      </p>
      <p class="contact-line">
        <svg viewBox="0 0 13 13" aria-hidden="true"><path d="M0 3h13v8H0zm1 .6 5.5 4 5.5-4z"/></svg>
        daniel@harborbuilders.com.au
      </p>
      <p class="contact-line">
        <svg viewBox="0 0 13 13" aria-hidden="true"><circle cx="6.5" cy="6.5" r="6.3"/><path d="M3 4.5 5.5 3.5 7 5.5 5 7.5 5.5 10 3.5 8.5zM8 3l2 1.5L9.5 7 8 6z" fill="#f3f3f3"/></svg>
        www.harborbuilders.com.au
      </p>
    </div>
  </section>

  <section class="card card-back">
    <div class="brand"><span class="brand-mark"></span>Harbor Builders</div>
    <p class="url-back">www.harborbuilders.com.au</p>
  </section>
</body>
</html>
```